Etikett für Likörflasche - Tinderbox
Zielgruppe
Wir sind eine kleine Tinderbox / Likörmanufaktur. Unser Obst für die Brände und Liköre stammt aus eigenem Anbau bzw. von umliegenden regionalen Bauern. Hier setzen wir auf sehr gute Qualität und verwenden keine Zusatzstoffe, Geschmacksverstärker, Farbstoffe etc. Im ersten Schritt werden wir nur 3-4 verschiedene Liköre anbieten.
Wir möchten unsere Liköre zukünftig auf Veranstaltungen / Events und Märkten verkaufen. Hierfür suchen wir ein pfiffiges und ansprechendes Etikettendesign.
Das Wort 'Tinderbox' soll die Leute auf den Events zu uns führen. Das wird auch mit großen Fahnen am Verkaufsstand beworben. Da wir auch ein paar amerikanische Foodtrucks haben soll auch das Etikett ein bisschen amerikanisch gehalten werden.
Zielgruppe: 28 bis 55 Jahre (Männer & Frauen)
Verkaufspreis pro 0,5 Liter Flasche ca. 24,50 Euro
Aufgabenstellung
Es soll ein Etikett auf die Flasche (nur vorne nicht auf die Rückseite).
Etikettengröße: ca. 7,0 x 8,5cm (für die 0,5l Flasche)
Angaben die sich auf dem Etikett ändern:
- Inhalt entweder 0,35l oder 0,5l Flasche
- Bezeichnung vom Inhalt und 'Kurzbeschreibung'
- Alkoholgehalt
Ich habe in PowerPoint schon mal ein Etikett zusammen gestellt, auf dem die Angaben alle mit enthalten sind. Hier fehlt mir allerdings der Pfiff und das Professionelle. Auch die Darstellung der Eigenschaften wie 'Echte Früchte', 'Handcrafted' etc. gefällt mir so auch nicht. Vielleicht wäre auch noch ein cooler Spruch darauf gut.
In die Anlage habe ich meine kreierte PowerPoint Folie gepackt (auf der 2. Folie findet ihr die geplante Flasche in die abgefüllt wird). Die zweite Datei ist ein Design was meinen Vorstellungen schon gut nahe kommt aus dem Internet (hier gefallen mir die Linien, kleine Gimmicks etc. da passiert einfach was auf dem Etikett). Von der Art her würde mir dieser Style gut gefallen. Es soll nur nicht zu überladen und kitschig werden.
Likörsorten die es geben wird: Wir werden uns erstmal auf 3-4 Sorten beschränken.

```html
<!DOCTYPE html>
<html lang="de">
<head>
<meta charset="utf-8">
<title>Baron' Tinderbox – Etikett Rusty and Berry</title>
<link rel="stylesheet" href="https://fonts.googleapis.com/css2?family=Oswald:wght@400;500;600&family=Libre+Baskerville:wght@700&family=Caveat:wght@500&family=Permanent+Marker&display=swap">
<style>
  :root{
    --bg-top:#426887;
    --bg-bottom:#22344c;
    --paper-light:#f3e2b4;
    --paper-mid:#ead29a;
    --paper-dark:#d9bb7e;
    --navy:#262b55;
    --teal:#1ea3b5;
    --teal-dark:#138a9b;
    --sketch:rgba(58,170,180,.22);
    --white:#ffffff;
  }
  *{margin:0;padding:0;box-sizing:border-box}
  html,body{width:1200px;height:2400px;overflow:hidden}
  body{background:linear-gradient(180deg,var(--bg-top),var(--bg-bottom));position:relative;font-family:"Oswald",sans-serif}
  .label{position:absolute;left:52px;top:532px;width:730px;height:890px;transform:scale(1.5);transform-origin:0 0}
  .label-shape{position:absolute;inset:0}
  .label > *{position:absolute}
  .sketch{background:var(--sketch);filter:blur(2px)}
  .sketch-moon{left:560px;top:125px;width:105px;height:185px;border-radius:50%}
  .sketch-barrel{left:0;top:420px;width:245px;height:270px;border-radius:0 40px 40px 0}
  .sketch-wheat{left:500px;top:685px;width:170px;height:95px;border-radius:50%}
  .brand{left:0;width:730px;text-align:center;color:var(--navy);font-weight:600;text-transform:uppercase;line-height:1}
  .brand-small{top:95px;font-size:36px;letter-spacing:4px}
  .brand-main{top:135px;font-size:118px;letter-spacing:2px}
  .famous{left:40px;top:262px;font-family:"Permanent Marker",cursive;color:var(--teal);font-size:21px}
  .subtitle{left:0;width:730px;top:288px;text-align:center;color:var(--navy);font-size:30px;font-weight:500;font-variant:small-caps;line-height:1}
  .rule{height:2px;background:var(--navy)}
  .rule-a{left:145px;top:324px;width:440px}
  .rule-b{left:75px;top:332px;width:580px}
  .rule-c{left:75px;top:412px;width:580px}
  .product{left:0;width:730px;top:338px;text-align:center;font-family:"Libre Baskerville",serif;font-weight:700;color:var(--teal);font-size:56px;line-height:72px;letter-spacing:-1px}
  .star-small{top:360px;color:#555;font-size:20px}
  .star-l{left:34px}.star-r{left:682px}
  .description{left:0;width:730px;top:428px;text-align:center;color:var(--navy);font-size:27px;line-height:40px;font-weight:500;transform:scaleX(.85)}
  .claim{font-family:"Caveat",cursive;color:var(--teal);font-size:30px;line-height:32px}
  .claim-one{left:26px;top:460px}
  .claim-real{left:622px;top:458px}
  .claim-hand{left:98px;top:630px;font-size:28px}
  .claim-add{left:536px;top:645px;font-size:28px}
  .facts{left:115px;top:540px;width:502px;height:70px;border-radius:35px;background:var(--teal);border:3px solid var(--teal-dark);box-shadow:inset 0 0 0 3px var(--white);display:flex;justify-content:center;align-items:center;gap:38px;color:var(--white);font-size:36px;font-weight:500}
  .divider{top:648px;left:250px;width:240px;height:40px}
  .address{left:0;width:730px;top:696px;text-align:center;color:var(--navy);font-size:25px;line-height:31px;font-weight:500}
  .web{left:0;width:730px;top:800px;text-align:center;color:var(--navy);font-size:25px;font-weight:500}
</style>
</head>
<body>
  <div class="label">
    <svg class="label-shape" viewBox="0 0 730 890" width="730" height="890" aria-hidden="true">
      <defs>
        <radialGradient id="paper" cx="50%" cy="45%" r="70%">
          <stop offset="0" stop-color="var(--paper-light)"/>
          <stop offset=".7" stop-color="var(--paper-mid)"/>
          <stop offset="1" stop-color="var(--paper-dark)"/>
        </radialGradient>
      </defs>
      <path d="M0 140 L40 140 A325 140 0 0 1 690 140 L730 140 L730 690 L700 690 A335 200 0 0 1 30 690 L0 690 Z" fill="url(#paper)"/>
    </svg>

    <div class="sketch sketch-moon" role="img" aria-label="Feine Skizze einer Mondsichel"></div>
    <div class="sketch sketch-barrel" role="img" aria-label="Feine Skizze eines Holzfasses"></div>
    <div class="sketch sketch-wheat" role="img" aria-label="Feine Skizze einer Getreideähre"></div>

    <div class="brand brand-small">Baron'</div>
    <div class="brand brand-main">Tinderbox</div>
    <div class="famous">The Famous</div>
    <div class="subtitle">Seasoned Fruits</div>

    <div class="rule rule-a"></div>
    <div class="rule rule-b"></div>
    <div class="star-small star-l">★</div>
    <div class="product">RUSTY AND BERRY</div>
    <div class="star-small star-r">★</div>
    <div class="rule rule-c"></div>

    <div class="description">WILDE BEEREN TREFFEN AUF VIELSCHICHTIGE<br>NOTEN VON WHISKEY UND KARAMELL</div>
    <div class="claim claim-one">The One<br>&amp; Only</div>
    <div class="claim claim-real">Real<br>Taste</div>

    <div class="facts"><span>500 ML</span><span>22 % VOL.</span><span>44 PROOF</span></div>

    <div class="claim claim-hand">Complete<br>Handcrafted</div>
    <div class="claim claim-add">No Additives</div>

    <svg class="divider" viewBox="0 0 240 40" width="240" height="40" aria-hidden="true">
      <line x1="0" y1="20" x2="88" y2="20" stroke="var(--navy)" stroke-width="2"/>
      <line x1="152" y1="20" x2="240" y2="20" stroke="var(--navy)" stroke-width="2"/>
      <polygon points="120,0 125.9,13.8 140.9,15.2 129.6,25.1 132.9,39.8 120,32 107.1,39.8 110.4,25.1 99.1,15.2 114.1,13.8" fill="var(--navy)"/>
    </svg>

    <div class="address">BARON'S TINDERBOX<br>AM LINDENHANG 12<br>90411 ALTDORF</div>
    <div class="web">WWW.BARONS-TINDERBOX.DE</div>
  </div>
</body>
</html>
```